Harbor Ledger Funds Bus card and Logo

I need a logo design and Bus card design. The fund focuses on evaluating and investing in minerals (sub-surface rights) and real estate.

Harbor ledger refers to a book of knowledge that each plebe gets when entering the Kelmont Marine Academy (my alma mater)

Target Market(s)

Investors and financial advisors

Contact Information for Business Card

Simple - perhaps a logo with a theme on book of knowledge

Logo Text

Ex Scientia Imperium

Font styles to use
Serif
Sans Serif

Colors

Designer to choose colors to be used in the design.

Requirements
Must have
• memorable logo that is relatively simple

```html
<!DOCTYPE html>
<html lang="en">
<head>
<meta charset="utf-8">
<title>Harbor Ledger Funds – Business Cards</title>
<link rel="stylesheet" href="https://fonts.googleapis.com/css2?family=Open+Sans:wght@400;600;700&display=swap">
<style>
  :root {
    --backdrop: #3a322d;
    --card: #111111;
    --card-edge: #1c1c1c;
    --accent-green: #8dc63f;
    --accent-blue: #3aa0dc;
    --text-light: #e6e6e6;
    --text-muted: #b9b9b9;
    --silver: #cfcfcf;
    --rule: #3a3a3a;
  }
  * { box-sizing: border-box; margin: 0; padding: 0; }
  html, body {
    width: 1200px; height: 844px; overflow: hidden;
    background: var(--backdrop);
    font-family: "Open Sans", Arial, sans-serif;
  }
  .stage { position: relative; width: 1200px; height: 844px; }
  .card {
    position: absolute; top: 272px;
    width: 520px; height: 300px;
    background: var(--card);
    border: 1px solid var(--card-edge);
    box-shadow: 0 12px 30px rgba(0,0,0,.45);
  }
  .card--front { left: 60px; display: flex; }
  .card--back { left: 620px; display: flex; align-items: center; justify-content: center; }

  .brand { display: flex; align-items: center; gap: 12px; }
  .brand__dot { width: 34px; height: 34px; border-radius: 50%; background: var(--accent-blue); flex: none; }
  .brand__name {
    font-weight: 700; font-size: 22px; line-height: 1.15;
    letter-spacing: .02em; text-transform: uppercase;
    color: var(--text-light);
  }
  .card--back .brand__dot { background: var(--silver); }
  .card--back .brand__name { color: var(--silver); font-size: 26px; }

  .front__brand-area {
    width: 262px; display: flex; align-items: center; justify-content: center;
    padding-top: 60px;
  }
  .front__divider { width: 1px; background: var(--rule); margin: 70px 0 40px; }
  .front__details { padding: 62px 0 0 22px; }

  .person__name { color: var(--accent-green); font-weight: 700; font-size: 17px; letter-spacing: .01em; }
  .person__role { color: var(--text-muted); font-size: 12.5px; margin-bottom: 8px; }
  .contact { list-style: none; }
  .contact__item {
    display: flex; align-items: center; gap: 8px;
    color: var(--text-light); font-size: 12.5px; line-height: 19px;
  }
  .contact__icon { width: 11px; height: 11px; fill: var(--accent-green); flex: none; }
  .address { color: var(--text-light); font-size: 12.5px; line-height: 18px; margin: 8px 0 0 19px; }
</style>
</head>
<body>
<main class="stage">
  <section class="card card--front" aria-label="Business card, contact side">
    <div class="front__brand-area">
      <div class="brand">
        <span class="brand__dot"></span>
        <span class="brand__name">Harbor Ledger<br>Funds</span>
      </div>
    </div>
    <div class="front__divider"></div>
    <div class="front__details">
      <p class="person__name">DANIEL ARCHER</p>
      <p class="person__role">Managing Director</p>
      <ul class="contact">
        <li class="contact__item">
          <svg class="contact__icon" viewBox="0 0 12 12"><path d="M2 1h2.5l1 3-1.5 1a6 6 0 0 0 3 3l1-1.5 3 1V10a1 1 0 0 1-1 1A9 9 0 0 1 1 2a1 1 0 0 1 1-1z"/></svg>
          044-210 555 318
        </li>
        <li class="contact__item">
          <svg class="contact__icon" viewBox="0 0 12 12"><path d="M3.5 0h5a1 1 0 0 1 1 1v10a1 1 0 0 1-1 1h-5a1 1 0 0 1-1-1V1a1 1 0 0 1 1-1zm0 1.5v8h5v-8z"/></svg>
          044-210 555 319
        </li>
        <li class="contact__item">
          <svg class="contact__icon" viewBox="0 0 12 12"><path d="M0 2h12v8H0zm1 1v.3l5 3.2 5-3.2V3z"/></svg>
          info@harborledger.com
        </li>
        <li class="contact__item">
          <svg class="contact__icon" viewBox="0 0 12 12"><circle cx="6" cy="6" r="5.5"/></svg>
          www.harborledger.com
        </li>
      </ul>
      <p class="address">12345, Address Goes Here<br>Country Name, 123456.</p>
    </div>
  </section>

  <section class="card card--back" aria-label="Business card, brand side">
    <div class="brand">
      <span class="brand__dot"></span>
      <span class="brand__name">Harbor Ledger<br>Funds</span>
    </div>
  </section>
</main>
</body>
</html>
```